Business Cards for new orthopaedic surgery practice

My husband and I are starting our own orthopaedic surgery practice. We are looking for a business card that is uniform, but one will have my name/title and the other will have his. You can just create one design with my name on it for now. But when I choose your design as the winning design I will ask that you add another copy with his name/title.

We are looking for classy, simple, elite all in one. We like dark blues/a little gold/yellow. Something that goes with our logo. We want our logo incorporated. Here is all the info you need:
Business name: RV Bone & Vitality Center
Location: 38517 North Willowmere Ave
Maple Grove, FL 33490
Phone: 954-218-4063
Fax: 954-582-7341
Email: info@myrvbonecare.example

Names: Lydia Vance, M.D.
Board Certified Hand and Upper Extremity Surgeon

Ebo Dansu, M.D.
Board Certified Hip & Knee Replacement/General Orthopaedic Surgeon

Can decide what you want to put on the back. Maybe a slogan:
Grounded in Care. Built Around You

I am just going to upload our logo. The only thing is if we select you as the winning design, the location, and phone numbers may change. We will need your help to update that once fully solidified.

Industry/Entity Type

Medical

Contact Information for Business Card

Colors
0054AA
0677BA
7BADD7
CADEEF
E8F1F8
0094D4
00A9DD
6FCCEA
C7EBF8
E9F6FB

Requirements
Must have
• class, appeal,
Should not have
• We want to air on the side of masculine if we are looking at masculine vs. feminine feel. But we still want it classy, sophisticated, and something we will love

```html
<!DOCTYPE html>
<html lang="en">
<head>
<meta charset="utf-8">
<title>RV Bone &amp; Vitality Center — Business Card</title>
<link href="https://fonts.googleapis.com/css2?family=Figtree:wght@400;500;600&family=Libre+Baskerville:wght@700&display=swap" rel="stylesheet">
<style>
  :root {
    --stage: #1d1d1e;
    --navy: #1b2a52;
    --navy-soft: #24376a;
    --gold: #c7a05a;
    --paper: #f3f3f2;
    --ink: #1e1e1e;
    --white: #ffffff;
  }
  * { margin: 0; padding: 0; box-sizing: border-box; }
  html, body { width: 1200px; height: 1059px; overflow: hidden; background: var(--stage); }
  .stage { position: relative; width: 1200px; height: 1059px; }

  .card {
    position: absolute;
    width: 687px;
    height: 390px;
    border-radius: 18px;
    overflow: hidden;
    font-family: "Figtree", "Helvetica Neue", Arial, sans-serif;
  }
  .card--front { left: 257px; top: 89px; background: var(--paper); }
  .card--back  { left: 255px; top: 547px; background: var(--navy); }

  .wave { position: absolute; inset: 0; width: 100%; height: 100%; }

  .brand {
    position: absolute;
    left: 43px; top: 88px;
    width: 170px;
    text-align: center;
    color: var(--navy);
    font-weight: 600;
    font-size: 20px;
    line-height: 1.25;
    letter-spacing: 0.5px;
  }

  .identity { position: absolute; right: 33px; top: 48px; text-align: right; }
  .identity__name {
    font-family: "Libre Baskerville", "Times New Roman", serif;
    font-weight: 700;
    font-size: 22px;
    color: var(--gold);
    letter-spacing: 0.3px;
  }
  .identity__title {
    margin-top: 6px;
    font-size: 15px;
    line-height: 21px;
    color: var(--ink);
  }

  .contact { position: absolute; right: 33px; top: 215px; text-align: right; color: var(--white); font-size: 16px; }
  .contact__address { line-height: 24px; }
  .contact__list { list-style: none; margin-top: 20px; }
  .contact__item { display: flex; justify-content: flex-end; align-items: center; gap: 6px; height: 27px; }
  .contact__icon { width: 13px; height: 13px; fill: var(--gold); }

  .back-mark {
    position: absolute;
    left: 0; right: 0; top: 140px;
    text-align: center;
    color: var(--navy-soft);
    font-weight: 600;
    font-size: 34px;
    line-height: 1.2;
    letter-spacing: 1px;
  }
  .tagline {
    position: absolute;
    left: 0; right: 0; top: 334px;
    text-align: center;
    color: var(--gold);
    font-weight: 500;
    font-size: 19px;
  }
</style>
</head>
<body>
<main class="stage">

  <section class="card card--front">
    <svg class="wave" viewBox="0 0 1168 663" preserveAspectRatio="none" aria-hidden="true">
      <path fill="#1b2a52" d="M0,438 C150,520 330,530 520,470 C700,410 880,270 1020,268 C1100,268 1140,290 1168,312 L1168,663 L0,663 Z"/>
      <path fill="#c7a05a" d="M0,378 C160,480 340,490 540,420 C700,365 830,270 930,248 C820,280 700,380 540,445 C340,520 160,510 0,410 Z"/>
      <path fill="#1b2a52" d="M210,538 C420,520 600,420 760,345 C880,290 960,255 1025,250 C950,262 880,290 780,340 C620,420 440,525 210,538 Z"/>
    </svg>

    <div class="brand">RV Bone &amp;<br>Vitality Center</div>

    <div class="identity">
      <h1 class="identity__name">LYDIA VANCE, M.D.</h1>
      <p class="identity__title">Board Certified Hand and Upper<br>Extremity Surgeon</p>
    </div>

    <div class="contact">
      <p class="contact__address">38517 North Willowmere Ave<br>Maple Grove, FL 33490</p>
      <ul class="contact__list">
        <li class="contact__item">954-218-4063
          <svg class="contact__icon" viewBox="0 0 24 24" aria-label="Phone"><path d="M6.6 10.8a15.1 15.1 0 0 0 6.6 6.6l2.2-2.2a1 1 0 0 1 1-.25 11.4 11.4 0 0 0 3.6.57 1 1 0 0 1 1 1V20a1 1 0 0 1-1 1A17 17 0 0 1 3 4a1 1 0 0 1 1-1h3.5a1 1 0 0 1 1 1c0 1.25.2 2.45.57 3.6a1 1 0 0 1-.25 1z"/></svg>
        </li>
        <li class="contact__item">954-582-7341
          <svg class="contact__icon" viewBox="0 0 24 24" aria-label="Fax"><path d="M6 2h12v5H6zM3 8h18a1 1 0 0 1 1 1v8h-4v5H6v-5H2V9a1 1 0 0 1 1-1zm5 8v4h8v-4z"/></svg>
        </li>
        <li class="contact__item">info@myrvbonecare.example
          <svg class="contact__icon" viewBox="0 0 24 24" aria-label="Email"><path d="M2 5h20v14H2zm2 2v.4l8 5.2 8-5.2V7z"/></svg>
        </li>
      </ul>
    </div>
  </section>

  <section class="card card--back">
    <div class="back-mark">RV Bone &amp;<br>Vitality Center</div>
    <p class="tagline">Grounded in Care. Built Around You</p>
  </section>

</main>
</body>
</html>
```